Business Cards for new orthopaedic surgery practice

My husband and I are starting our own orthopaedic surgery practice. We are looking for a business card that is uniform, but one will have my name/title and the other will have his. You can just create one design with my name on it for now. But when I choose your design as the winning design I will ask that you add another copy with his name/title.

We are looking for classy, simple, elite all in one. We like dark blues/a little gold/yellow. Something that goes with our logo. We want our logo incorporated. Here is all the info you need:
Business name: RV Bone & Vitality Center
Location: 38517 North Willowmere Ave
Maple Harbor, FL 33198
Phone: 954-218-4063
Fax: 954-582-7341
Email: info@myrvbonecare.example

Names: Lydia Vance, M.D.
Board Certified Hand and Upper Extremity Surgeon

Ebo Dansu, M.D.
Board Certified Hip & Knee Replacement/General Orthopaedic Surgeon

Can decide what you want to put on the back. Maybe a slogan:
Grounded in Skill. Centered on You

I am just going to upload our logo. The only thing is if we select you as the winning design, the location, and phone numbers may change. We will need your help to update that once fully solidified.

Industry/Entity Type

Medical

Contact Information for Business Card

Colors
0054AA
0677BA
7BADD7
CADEEF
E8F1F8
0094D4
00A9DD
6FCCEA
C7EBF8
E9F6FB

Requirements
Must have
• class, appeal,
Should not have
• We want to air on the side of masculine if we are looking at masculine vs. feminine feel. But we still want it classy, sophisticated, and something we will love

```html
<!DOCTYPE html>
<html lang="en">
<head>
<meta charset="utf-8">
<title>RV Bone & Vitality Center – Business Cards</title>
<link href="https://fonts.googleapis.com/css2?family=Poppins:wght@400;500;600&display=swap" rel="stylesheet">
<style>
  :root {
    --navy: #1b2753;
    --gold: #c9a15a;
    --ink: #1f2333;
    --paper: #ffffff;
    --backdrop: #e9ebef;
  }
  * { box-sizing: border-box; margin: 0; padding: 0; }
  html, body { width: 1200px; height: 900px; overflow: hidden; }
  body {
    background: var(--backdrop);
    font-family: "Poppins", sans-serif;
    position: relative;
  }
  .card {
    position: absolute;
    left: 260px;
    width: 680px;
    height: 390px;
    border-radius: 22px;
    overflow: hidden;
    box-shadow: 0 10px 28px rgba(0,0,0,0.18);
  }
  /* Front */
  .card-front { top: 45px; background: var(--navy); color: var(--paper); }
  .front-brand {
    position: absolute; left: 50%; top: 70px; transform: translateX(-50%);
    width: 230px; height: 230px; display: flex; align-items: center; justify-content: center;
  }
  .brand-ring { position: absolute; inset: 0; }
  .brand-name {
    position: relative; font-weight: 600; text-align: center;
    font-size: 26px; line-height: 1.2; letter-spacing: 0.5px;
  }
  .card-front .brand-name { color: var(--paper); }
  .slogan {
    position: absolute; left: 0; right: 0; top: 322px; text-align: center;
    font-size: 16px; letter-spacing: 0.3px;
  }
  /* Back */
  .card-back { top: 465px; background: var(--paper); color: var(--ink); }
  .back-brand {
    position: absolute; left: 40px; top: 40px; width: 230px; height: 230px;
    display: flex; align-items: center; justify-content: center;
  }
  .card-back .brand-name { color: var(--navy); }
  .divider {
    position: absolute; left: 300px; top: 40px; width: 1.5px; height: 250px; background: var(--gold);
  }
  .details { position: absolute; left: 325px; top: 38px; right: 20px; }
  .doctor-name { color: var(--gold); font-weight: 600; font-size: 24px; line-height: 1.1; }
  .doctor-title { font-size: 14px; line-height: 1.25; margin-bottom: 10px; }
  .contact-list { list-style: none; margin-top: 6px; }
  .contact-list li { display: flex; align-items: center; gap: 10px; font-size: 14px; line-height: 1.45; }
  .contact-list svg { width: 13px; height: 13px; fill: var(--gold); flex: none; }
  .address-band {
    position: absolute; left: 0; right: 0; bottom: 0; height: 62px; background: var(--navy);
    color: var(--paper); display: flex; align-items: center; justify-content: center;
    font-size: 16px; letter-spacing: 0.3px;
  }
</style>
</head>
<body>

  <section class="card card-front" aria-label="Card front">
    <div class="front-brand">
      <svg class="brand-ring" viewBox="0 0 230 230" aria-hidden="true">
        <circle cx="115" cy="115" r="112" fill="none" stroke="var(--gold)" stroke-width="2"/>
      </svg>
      <p class="brand-name">RV Bone &amp;<br>Vitality<br>Center</p>
    </div>
    <p class="slogan">Grounded in Skill. Centered on You</p>
  </section>

  <section class="card card-back" aria-label="Card back">
    <div class="back-brand">
      <svg class="brand-ring" viewBox="0 0 230 230" aria-hidden="true">
        <circle cx="115" cy="115" r="112" fill="none" stroke="var(--gold)" stroke-width="2"/>
      </svg>
      <p class="brand-name">RV Bone &amp;<br>Vitality<br>Center</p>
    </div>
    <div class="divider"></div>
    <div class="details">
      <h2 class="doctor-name">Lydia Vance, M.D.</h2>
      <p class="doctor-title">Board Certified Hand and<br>Upper Extremity Surgeon</p>
      <h2 class="doctor-name">Ebo Dansu, M.D.</h2>
      <p class="doctor-title">Board Certified Hip &amp; Knee Replacement<br>/General Orthopaedic Surgeon</p>
      <ul class="contact-list">
        <li><svg viewBox="0 0 16 16"><path d="M3 1h3l1.5 4-2 1.2a9 9 0 0 0 4.3 4.3L11 8.5l4 1.5v3a2 2 0 0 1-2 2A12 12 0 0 1 1 3a2 2 0 0 1 2-2z"/></svg>954-218-4063</li>
        <li><svg viewBox="0 0 16 16"><path d="M4 1h7v4H4zM2 6h12v7H2zM4 11h8v4H4z"/></svg>954-582-7341</li>
        <li><svg viewBox="0 0 16 16"><path d="M1 3h14v10H1zM1 3l7 6 7-6" stroke="#fff" stroke-width="1"/></svg>info@myrvbonecare.example</li>
        <li><svg viewBox="0 0 16 16"><circle cx="8" cy="8" r="7"/></svg>www.rvbonecare.example</li>
      </ul>
    </div>
    <div class="address-band">38517 North Willowmere Ave, Maple Harbor, FL 33198</div>
  </section>

</body>
</html>
```